Change of trading name, rebrand

existing website to be updated with new theme and logo. existing website is
www.harlowbrentmere.com.au
Industry/Entity Type
Construction
Coding
Coded - Design and coding required
Number of Pages Required
5+ page
Requirements
Must have
- be mobile phone friendly

```html
<!DOCTYPE html>
<html lang="en">
<head>
<meta charset="utf-8">
<title>HBR Plant Hire</title>
<link href="https://fonts.googleapis.com/css2?family=Poppins:wght@400;500;600;700;800&display=swap" rel="stylesheet">
<style>
:root{
  --navy:#2f3470;
  --navy-dark:#262a5c;
  --ink:#222;
  --dark:#2f2f2f;
  --darker:#2a2a2a;
  --grey:#5a5a5a;
  --line:#d9d9d9;
  --white:#fff;
}
*{margin:0;padding:0;box-sizing:border-box}
html,body{width:1200px;height:4525px;overflow:hidden}
body{position:relative;font-family:'Poppins',sans-serif;color:var(--ink);background:var(--white)}
.abs{position:absolute}
.slant-btn{position:absolute;display:flex;align-items:center;padding-left:16px;font-size:13px;font-weight:600;clip-path:polygon(0 0,84% 0,100% 100%,0 100%)}
.photo{position:absolute}
.heading{position:absolute;font-size:42px;font-weight:400;color:var(--ink);white-space:nowrap}
.heading b{color:var(--navy);font-weight:700}
.heading .dash{display:inline-block;width:58px;height:4px;background:var(--ink);vertical-align:middle;margin-left:4px;transform:translateY(10px)}

/* header */
.topbar{left:483px;top:0;width:717px;height:61px;background:var(--navy);clip-path:polygon(0 0,100% 0,100% 100%,40px 100%)}
.topbar-item{position:absolute;top:22px;color:#fff;font-size:12px;display:flex;align-items:center;gap:10px;white-space:nowrap}
.topbar-div{position:absolute;top:10px;width:1px;height:40px;background:rgba(255,255,255,.6)}
.soc{display:inline-block;width:19px;height:19px;border-radius:50%;background:#fff;margin-left:4px}
.brand{left:115px;top:22px;color:var(--navy);font-weight:800;text-align:center;line-height:1}
.brand .big{font-size:44px;letter-spacing:2px}
.brand .small{font-size:13px;letter-spacing:5px;margin-top:4px}
.nav{position:absolute;top:93px;font-size:12px;color:var(--ink);font-weight:500;white-space:nowrap}
.nav.active{color:var(--navy);text-decoration:underline;text-underline-offset:4px}
.nav-cta{left:966px;top:81px;width:122px;height:42px;background:#1b1b1b;color:#fff;font-size:12px;font-weight:500}

/* hero */
.hero-bg{left:0;top:134px;width:1200px;height:586px;background:var(--navy)}
.hero-photo{left:466px;top:134px;width:734px;height:586px;background:linear-gradient(160deg,#3d80c8 0%,#9cc3e3 30%,#a9a291 55%,#6d6458 100%);clip-path:polygon(228px 0,100% 0,100% 100%,0 100%)}
.hero-text{left:111px;color:#fff;white-space:nowrap}
.swap-btn{left:570px;top:384px;width:50px;height:50px;border-radius:50%;background:#fff;display:flex;align-items:center;justify-content:center}

/* about */
.about-photo{left:111px;top:803px;width:504px;height:448px;background:linear-gradient(165deg,#8fbbe6 0%,#dbe7f1 35%,#b7aa93 65%,#8a8170 100%)}
.about-wedge{left:316px;top:803px;width:300px;height:448px;background:var(--navy);clip-path:polygon(0 0,10% 0,80% 100%,68% 100%)}
.about-wedge-white{left:332px;top:803px;width:290px;height:448px;background:#fff;clip-path:polygon(0 0,100% 0,100% 100%,95% 100%,0 0)}
.about-copy{left:642px;top:922px;width:450px;font-size:12.5px;line-height:29px;color:var(--grey)}
.about-copy p+p{margin-top:12px}

/* stats */
.stats-photo{left:610px;top:1339px;width:590px;height:411px;background:linear-gradient(180deg,#4d86c4 0%,#8db4dc 40%,#c79a55 70%,#a77a40 100%)}
.stats-band{left:0;top:1379px;width:990px;height:329px;background:var(--dark);clip-path:polygon(0 0,852px 0,984px 100%,0 100%)}
.stat{position:absolute;top:1476px;color:#fff;white-space:nowrap}
.stat .dot{width:36px;height:36px;border-radius:50%;background:#8a8a8a}
.stat .num{font-size:30px;font-weight:500;margin-top:30px;line-height:1}
.stat .lbl{font-size:12px;margin-top:10px}
.stat .lbl2{font-size:15px;line-height:28px;margin-top:44px}
.stat-div{position:absolute;top:1481px;height:132px;border-left:2px dotted #fff}

/* services */
.card{position:absolute;top:1942px;width:320px;height:448px;clip-path:polygon(0 44px,100% 0,100% 100%,0 100%)}
.card-title{position:absolute;bottom:22px;left:0;right:0;text-align:center;color:#fff;font-size:24px;font-weight:600}
.card-mid{background:linear-gradient(180deg,#3a3e72 0%,#484d86 100%);color:#fff;text-align:center}
.card-mid h3{margin-top:128px;font-size:28px;font-weight:500}
.card-mid p{margin:22px 22px 0;font-size:13.5px;line-height:29px}
.card-btn{left:94px;top:372px;width:122px;height:42px;background:#fff;color:var(--ink)}
.arrow{position:absolute;top:2163px}

/* policies */
.policy-band{left:0;top:2474px;width:1200px;height:299px;background:linear-gradient(180deg,#3a3a3a,#2e2e2e)}
.policy{position:absolute;top:2621px;width:258px;height:85px;background:#fff;clip-path:polygon(0 0,83% 0,100% 100%,0 100%);display:flex;align-items:center;padding-left:16px;gap:14px;font-size:20px;font-weight:500;line-height:1.2}

/* partners */
.partner{position:absolute;top:2970px;font-size:34px;font-weight:600;color:var(--grey);width:190px;text-align:center}
.partner-box{left:512px;top:2953px;width:228px;height:72px;background:#fff;box-shadow:0 4px 14px rgba(0,0,0,.15)}

/* contact */
.contact-band{left:0;top:3131px;width:1200px;height:520px;background:var(--dark)}
.contact-photo{left:0;top:3131px;width:611px;height:520px;background:linear-gradient(175deg,#5f7fa6 0%,#3f5a3a 35%,#c9c7c0 70%,#6f6b63 100%);clip-path:polygon(0 0,436px 0,611px 100%,0 100%)}
.field{position:absolute;background:#fff;font-size:12px;color:#777;padding:13px 20px}

/* cta */
.cta-photo{left:624px;top:3696px;width:536px;height:310px;border-radius:40% 50% 30% 40%;background:radial-gradient(ellipse at 55% 45%,#e8b830 0%,#d9a523 45%,rgba(230,230,230,.6) 80%,#fff 100%)}

/* footer */
.footer{left:0;top:4094px;width:1200px;height:431px;background:var(--darker)}
.f-head{position:absolute;top:4180px;color:#fff;font-size:20px;font-weight:500}
.f-list{position:absolute;top:4232px;list-style:none;color:#fff;font-size:12px;line-height:29px}
.f-contact{position:absolute;left:871px;color:#fff;font-size:12px;display:flex;align-items:center;gap:22px;white-space:nowrap}
.map{left:111px;top:4305px;width:233px;height:166px;background:linear-gradient(135deg,#e9ecef,#d6dde3)}
</style>
</head>
<body>

<!-- header -->
<div class="abs topbar"></div>
<div class="topbar-item" style="left:553px"><svg width="14" height="14" viewBox="0 0 24 24" fill="#fff"><path d="M6.6 10.8a15 15 0 006.6 6.6l2.2-2.2a1 1 0 011-.25 11 11 0 003.6.6 1 1 0 011 1V20a1 1 0 01-1 1A17 17 0 013 4a1 1 0 011-1h3.5a1 1 0 011 1 11 11 0 00.6 3.6 1 1 0 01-.25 1z"/></svg>1300 555 014</div>
<div class="topbar-div" style="left:689px"></div>
<div class="topbar-item" style="left:718px"><svg width="14" height="12" viewBox="0 0 24 18" fill="#fff"><path d="M0 0h24v18H0zM2 2l10 7 10-7z" fill-rule="evenodd"/></svg>info@hbrplant.com.au</div>
<div class="topbar-div" style="left:893px"></div>
<div class="topbar-item" style="left:919px">Follow Us:<span><span class="soc"></span><span class="soc"></span><span class="soc"></span><span class="soc"></span></span></div>

<div class="abs brand"><div class="big">HBR</div><div class="small">PLANT HIRE</div></div>

<span class="nav active" style="left:462px">Home</span>
<span class="nav" style="left:522px">About Us</span>
<span class="nav" style="left:601px">Plant Hire <svg width="10" height="6" viewBox="0 0 10 6"><path d="M0 0h10L5 6z" fill="#999"/></svg></span>
<span class="nav" style="left:692px">Major Project Snapshot</span>
<span class="nav" style="left:850px">Policies</span>
<span class="nav" style="left:919px">Jobs</span>
<div class="slant-btn nav-cta">Contact Us</div>

<!-- hero -->
<div class="abs hero-bg"></div>
<div class="photo hero-photo" role="img" aria-label="Excavator loaded on a low loader trailer under a blue sky"></div>
<div class="abs hero-text" style="top:236px;font-size:23px">Welcome To</div>
<div class="abs hero-text" style="top:288px;font-size:32px;font-weight:500">HBR PLANT HIRE</div>
<div class="abs hero-text" style="top:338px;font-size:50px;font-weight:700;line-height:64px">Your Perfect<br>Collaborator on<br>any Project.</div>
<div class="slant-btn" style="left:111px;top:571px;width:124px;height:40px;background:#fff;color:var(--ink)">Get Started</div>
<div class="slant-btn" style="left:250px;top:571px;width:122px;height:40px;background:#fff;color:#fff;padding-left:0"><div style="position:absolute;inset:2px;background:var(--navy);clip-path:polygon(0 0,83% 0,99% 100%,0 100%);display:flex;align-items:center;padding-left:14px">Read More</div></div>
<div class="abs swap-btn"><svg width="24" height="24" viewBox="0 0 24 24" fill="none" stroke="#222" stroke-width="2"><path d="M5 8h13l-4-4M19 16H6l4 4"/></svg></div>

<!-- about -->
<div class="photo about-photo" role="img" aria-label="Orange wheeled excavator on a work site"></div>
<div class="abs about-wedge-white"></div>
<div class="abs about-wedge"></div>
<div class="heading" style="left:642px;top:798px">About <b>Us</b><span class="dash"></span></div>
<div class="abs" style="left:642px;top:862px;font-size:24px;font-weight:700;color:var(--navy)">HBR HEAVY EQUIPMENT</div>
<div class="abs about-copy">
  <p>Harlow Brentmere Resources Pty Ltd trading as HBR Heavy Equipment is a privately owned company that was established in 2010. Our founder saw a need in the market for a plant and equipment supplier who was committed to the successful delivery of client's projects.</p>
  <p>With this vision and focus HBR has successfully seen our clients deliver on-time and on- budget. Taking the time to understand our clients requirements and what they are trying to achieve has allowed HBR to mature into the company it is today.</p>
</div>
<div class="slant-btn" style="left:641px;top:1177px;width:122px;height:42px;background:var(--navy);color:#fff">Read More</div>

<!-- stats -->
<div class="photo stats-photo" role="img" aria-label="Row of earthmoving machines in a yard at sunset"></div>
<div class="abs stats-band"></div>
<div class="stat" style="left:46px"><div class="dot"></div><div class="num">20+</div><div class="lbl">Years Of Experience</div></div>
<div class="stat-div" style="left:195px"></div>
<div class="stat" style="left:230px"><div class="dot"></div><div class="num">100+</div><div class="lbl">Machines in Fleet</div></div>
<div class="stat-div" style="left:367px"></div>
<div class="stat" style="left:395px"><div class="dot"></div><div class="lbl2">One Of QLD's<br>Largest Suppliers</div></div>
<div class="stat-div" style="left:564px"></div>
<div class="stat" style="left:606px"><div class="dot"></div><div class="lbl2" style="margin-top:36px">Onsite<br>Servicing</div></div>
<div class="stat-div" style="left:712px"></div>
<div class="stat" style="left:747px"><div class="dot"></div><div class="lbl2" style="margin-top:36px">Custom Machine<br>Attachments</div></div>

<!-- services -->
<div class="heading" style="left:436px;top:1824px">Our <b>Services</b><span class="dash"></span></div>
<svg class="arrow" style="left:40px" width="34" height="30" viewBox="0 0 34 30" fill="none" stroke="#999" stroke-width="3"><path d="M32 15H4M14 4L3 15l11 11"/></svg>
<svg class="arrow" style="left:1124px" width="34" height="30" viewBox="0 0 34 30" fill="none" stroke="#999" stroke-width="3"><path d="M2 15h28M20 4l11 11-11 11"/></svg>
<div class="card" style="left:111px;background:linear-gradient(180deg,#7fb0dd 0%,#c9d3d6 30%,#b58560 60%,#4a3a2e 100%)" role="img" aria-label="Orange excavator on a construction site"><div class="card-title">Excavator Hire</div></div>
<div class="card card-mid" style="left:437px">
  <h3>Dozer Hire</h3>
  <p>We have Kestrel and Ironbark dozers for hire – in a range of sizes suitable for projects from detailed to bulk earthworks. We also offer swampy dozers in both K5 and K6 sizes for hire.</p>
  <div class="slant-btn card-btn">Read More</div>
</div>
<div class="card" style="left:764px;background:linear-gradient(180deg,#3e8ad2 0%,#9cc6ea 35%,#4a4a4a 65%,#2a2a2a 100%)" role="img" aria-label="Wheel loader beside stacked pipes"><div class="card-title">Loaders Hire</div></div>

<!-- policies -->
<div class="abs policy-band"></div>
<div class="heading" style="left:441px;top:2520px;color:#fff">Our <b style="color:#fff">Policies</b><span class="dash" style="background:#fff"></span></div>
<div class="policy" style="left:76px"><svg width="40" height="40" viewBox="0 0 40 40"><circle cx="18" cy="20" r="15" fill="none" stroke="var(--navy)" stroke-width="3"/><path d="M14 20h8M18 16v8" stroke="var(--navy)" stroke-width="3"/><circle cx="30" cy="30" r="7" fill="var(--navy)"/></svg>Health &amp;<br>Safety</div>
<div class="policy" style="left:348px"><svg width="36" height="36" viewBox="0 0 36 36"><circle cx="18" cy="18" r="16" fill="var(--navy)"/><path d="M8 12c6 2 8 8 4 14M22 6c-2 6 4 8 10 10" stroke="#fff" stroke-width="2" fill="none"/></svg>Environmental</div>
<div class="policy" style="left:618px"><svg width="40" height="40" viewBox="0 0 40 40" fill="var(--navy)"><circle cx="8" cy="8" r="4"/><circle cx="20" cy="8" r="4"/><circle cx="32" cy="8" r="4"/><circle cx="8" cy="20" r="4"/><circle cx="20" cy="20" r="4"/><circle cx="32" cy="20" r="4"/><circle cx="8" cy="32" r="4"/><circle cx="20" cy="32" r="4"/><circle cx="32" cy="32" r="4"/></svg>Rehabilitation</div>
<div class="policy" style="left:891px"><svg width="40" height="42" viewBox="0 0 40 42" fill="var(--navy)"><path d="M4 6h18v36H4zM24 16h12v26H24z"/><path d="M8 10h4v4H8zM14 10h4v4h-4zM8 18h4v4H8zM14 18h4v4h-4zM8 26h4v4H8zM14 26h4v4h-4z" fill="#fff"/></svg>Commercial &amp;<br>Credit</div>

<!-- partners -->
<div class="heading" style="left:437px;top:2854px">Our <b>Partners</b><span class="dash"></span></div>
<div class="abs partner-box"></div>
<div class="partner" style="left:62px">Corvan</div>
<div class="partner" style="left:317px">Lattice</div>
<div class="partner" style="left:531px">Ridgeway</div>
<div class="partner" style="left:760px">Tallis</div>
<div class="partner" style="left:985px">Marlow</div>

<!-- contact -->
<div class="abs contact-band"></div>
<div class="photo contact-photo" role="img" aria-label="Street sweeper truck parked in front of trees"></div>
<div class="heading" style="left:704px;top:3166px;color:#fff">Contact <b style="color:#fff">Us</b><span class="dash" style="background:#fff"></span></div>
<div class="field" style="left:603px;top:3271px;width:270px;height:50px">Name</div>
<div class="field" style="left:882px;top:3271px;width:269px;height:50px">Phone</div>
<div class="field" style="left:603px;top:3333px;width:548px;height:49px">Email</div>
<div class="field" style="left:603px;top:3391px;width:548px;height:116px">Message</div>
<div class="slant-btn" style="left:817px;top:3540px;width:130px;height:40px;background:#fff;color:var(--ink);padding-left:24px">Submit Now</div>

<!-- cta -->
<div class="photo cta-photo" role="img" aria-label="Yellow tracked excavator"></div>
<div class="abs" style="left:113px;top:3770px;font-size:40px;color:var(--ink);white-space:nowrap">Contact us today for a</div>
<div class="abs" style="left:113px;top:3826px;font-size:42px;font-weight:700;color:var(--navy)">FREE QUOTE</div>
<div class="slant-btn" style="left:111px;top:3906px;width:130px;height:42px;background:var(--navy);color:#fff">Get a Quote</div>

<!-- footer -->
<div class="abs footer"></div>
<div class="abs brand" style="left:124px;top:4180px;color:#fff"><div class="big" style="font-size:56px">HBR</div><div class="small" style="font-size:15px">PLANT HIRE</div></div>
<div class="photo map" role="img" aria-label="Location map showing the depot"></div>

<div class="f-head" style="left:425px">Quick Links</div>
<ul class="f-list" style="left:430px"><li>Home</li><li>About Us</li><li>Plant Hire</li><li>Major Project Snapshot</li><li>Policies</li><li>Jobs</li><li>Contact Us</li></ul>

<div class="f-head" style="left:645px">Help Links</div>
<ul class="f-list" style="left:650px"><li>Privacy Policy</li><li>Terms &amp; Conditions</li><li>Disclaimer</li></ul>
<div class="f-head" style="left:645px;top:4342px">Follow Us</div>
<div class="abs" style="left:644px;top:4386px"><span class="soc" style="width:22px;height:22px;margin:0 6px 0 0"></span><span class="soc" style="width:22px;height:22px;margin:0 6px 0 0"></span><span class="soc" style="width:22px;height:22px;margin:0 6px 0 0"></span><span class="soc" style="width:22px;height:22px;margin:0"></span></div>

<div class="f-head" style="left:863px">Contact Us</div>
<div class="f-contact" style="top:4236px"><svg width="16" height="22" viewBox="0 0 16 22" fill="#fff"><path d="M8 0a8 8 0 018 8c0 6-8 14-8 14S0 14 0 8a8 8 0 018-8zm0 5a3 3 0 100 6 3 3 0 000-6z"/></svg>48 Wattle Rd, &nbsp;Carrick QLD 4210</div>
<div class="f-contact" style="top:4291px"><svg width="18" height="18" viewBox="0 0 24 24" fill="#fff"><path d="M6.6 10.8a15 15 0 006.6 6.6l2.2-2.2a1 1 0 011-.25 11 11 0 003.6.6 1 1 0 011 1V20a1 1 0 01-1 1A17 17 0 013 4a1 1 0 011-1h3.5a1 1 0 011 1 11 11 0 00.6 3.6 1 1 0 01-.25 1z"/></svg>1300 555 014</div>
<div class="f-contact" style="top:4341px"><svg width="18" height="14" viewBox="0 0 24 18" fill="#fff"><path d="M0 0h24v18H0zM2 2l10 7 10-7z" fill-rule="evenodd"/></svg>info@hbrplant.com.au</div>
<div class="f-contact" style="top:4400px"><svg width="18" height="16" viewBox="0 0 24 20" fill="#fff"><path d="M6 0h12v5H6zM2 6h20a2 2 0 012 2v7h-5v5H5v-5H0V8a2 2 0 012-2zm5 8v4h10v-4z" fill-rule="evenodd"/></svg>07 3000 0172</div>

<div class="abs" style="left:111px;top:4489px;width:978px;height:1px;background:rgba(255,255,255,.5)"></div>
<div class="abs" style="left:0;top:4500px;width:1200px;text-align:center;color:#fff;font-size:11px">Copyright © 2024 &nbsp;HBR Plant Hire. All rights reserved.</div>

</body>
</html>
```